QVR business card

Need a business card for a company that provides instructional design and elearning development services. The website is here: http://quorvane.studio/

I'm attaching a current logo, as well as the old business card design. While I like to keep it clean, the old design is too simplistic for my liking. The only idea I want to reuse from the old design is placing industry jargon on the back of the card, just need a better way to present it. But if you have other ideas for the back--feel free to experiment.

Please use the colors complementary to the color we have on the website. Thank you!

```html
<!DOCTYPE html>
<html lang="en">
<head>
<meta charset="utf-8">
<title>QVR Business Card</title>
<link rel="stylesheet" href="https://fonts.googleapis.com/css2?family=Open+Sans:wdth,wght@75..100,300..800&display=swap">
<style>
  :root {
    --teal: #1cb3ad;
    --teal-dark: #139d98;
    --gold: #d3c48c;
    --gold-text: #c9b774;
    --ink: #333538;
    --rule: #c8c8c8;
    --paper: #ffffff;
    --backdrop: #e9e9e9;
  }
  * { margin: 0; padding: 0; box-sizing: border-box; }
  html, body { width: 1200px; height: 726px; overflow: hidden; }
  body {
    background: var(--backdrop);
    font-family: "Open Sans", Arial, sans-serif;
    position: relative;
  }
  .card {
    position: absolute;
    top: 208px;
    width: 540px;
    height: 309px;
    box-shadow: 0 6px 18px rgba(0,0,0,0.14);
    overflow: hidden;
  }
  /* Front */
  .card-front { left: 40px; background: var(--paper); }
  .brand {
    position: absolute;
    top: 52px;
    left: 250px;
    display: flex;
    align-items: center;
    gap: 10px;
  }
  .brand-dot { width: 26px; height: 26px; border-radius: 50%; background: var(--teal); }
  .brand-name { font-size: 40px; font-weight: 700; color: var(--gold-text); letter-spacing: 1px; }
  .brand-rule {
    position: absolute; top: 118px; left: 250px; right: 36px;
    height: 1px; background: var(--rule);
  }
  .bands { position: absolute; left: 0; top: 0; width: 540px; height: 309px; }
  .site {
    position: absolute; top: 205px; left: 318px;
    font-size: 15px; line-height: 22px; letter-spacing: 2.5px; color: #fff;
  }
  .person { position: absolute; left: 38px; top: 144px; }
  .person-name { font-size: 15px; font-weight: 700; letter-spacing: 0.5px; color: var(--teal-dark); }
  .person-name .last { color: var(--gold-text); }
  .person-role { font-size: 13px; color: var(--ink); margin-top: 2px; }
  .contact { position: absolute; left: 38px; top: 196px; }
  .contact-row { display: flex; align-items: center; gap: 8px; font-size: 13.5px; color: var(--ink); height: 22px; }
  .contact-icon { width: 17px; height: 17px; }

  /* Back */
  .card-back {
    left: 620px;
    background: var(--teal);
    color: #fff;
  }
  .ask {
    position: absolute; left: 30px; top: 44px;
    font-size: 54px; font-weight: 800; line-height: 0.98; text-transform: uppercase;
  }
  .divider {
    position: absolute; left: 226px; top: 34px; bottom: 34px;
    width: 2px; background: rgba(255,255,255,0.85);
  }
  .jargon {
    position: absolute; left: 246px; top: 34px;
    list-style: none;
    font-stretch: 75%;
    font-weight: 500;
    font-size: 27px;
    line-height: 40.5px;
    text-transform: uppercase;
    white-space: nowrap;
  }
</style>
</head>
<body>
  <section class="card card-front" aria-label="Card front">
    <div class="brand">
      <span class="brand-dot"></span>
      <span class="brand-name">QVR</span>
    </div>
    <div class="brand-rule"></div>

    <svg class="bands" viewBox="0 0 540 309" aria-hidden="true">
      <polygon points="308,200 540,200 540,232 296,232" fill="var(--teal)"/>
      <polygon points="0,250 280,250 292,236 540,236 540,242 296,242 284,256 0,256" fill="var(--gold)"/>
      <rect x="0" y="266" width="540" height="22" fill="var(--teal)"/>
    </svg>
    <div class="site">www.quorvane.studio</div>

    <div class="person">
      <div class="person-name">MARLOW <span class="last">KESTRANE</span></div>
      <div class="person-role">Managing Director</div>
    </div>

    <div class="contact">
      <div class="contact-row">
        <svg class="contact-icon" viewBox="0 0 17 17" aria-hidden="true">
          <rect width="17" height="17" rx="2" fill="var(--teal)"/>
          <path d="M4 6c0-1 1-2 4.5-2S13 5 13 6l-1.5 1L10 6V5.5H7V6L5.5 7z M5 9h7v4H5z" fill="#fff"/>
        </svg>
        <span>555-013-2847</span>
      </div>
      <div class="contact-row">
        <svg class="contact-icon" viewBox="0 0 17 17" aria-hidden="true">
          <rect width="17" height="17" rx="2" fill="var(--teal)"/>
          <rect x="3.5" y="5" width="10" height="7" fill="none" stroke="#fff" stroke-width="1.3"/>
          <path d="M3.5 5l5 4 5-4" fill="none" stroke="#fff" stroke-width="1.3"/>
        </svg>
        <span>mkestrane@quorvane.studio</span>
      </div>
    </div>
  </section>

  <section class="card card-back" aria-label="Card back">
    <h2 class="ask">How<br>Can<br>We<br>Help?</h2>
    <div class="divider"></div>
    <ul class="jargon">
      <li>Mobile Learning SCORM</li>
      <li>Instructional Design LMS</li>
      <li>MOOCs eLearning HTML5</li>
      <li>Adult Learning Theory</li>
      <li>Gamification Classroom</li>
      <li>xAPI Blended Learning</li>
    </ul>
  </section>
</body>
</html>
```